Business Card Design using new attached logo

We are a family run Plumbing and Heating firm looking to improve our company image with an improved business card and new logo.We are looking to keep the company colour (Blue) involved in our design

Reason: New logo added which needs to be incorporated on designs

Industry/Entity Type

Business

Contact Information for Business Card

See attachment of all info required.

Requirements
Must have
• We have just picked a new company logo which is attached.
• Could you please provide your business card designs using this logo.
• We are looking for the logo on the back as well as the front with all the info required

```html
<!DOCTYPE html>
<html lang="en">
<head>
<meta charset="utf-8">
<title>Kestrel Services – Business Card</title>
<link href="https://fonts.googleapis.com/css2?family=Cinzel:wght@600&family=Source+Sans+3:ital,wght@0,400;0,600;1,400&display=swap" rel="stylesheet">
<style>
  :root {
    --backdrop: #333333;
    --navy: #1f3a78;
    --blue: #2f6db5;
    --bright: #3c8ad0;
    --ink: #1d1d1d;
    --rule: #c9c9c9;
    --white: #ffffff;
  }
  * { margin: 0; padding: 0; box-sizing: border-box; }
  html, body { width: 1200px; height: 907px; overflow: hidden; background: var(--backdrop); }
  body { position: relative; font-family: "Source Sans 3", Arial, sans-serif; }

  .card {
    position: absolute; left: 300px; width: 600px; height: 343px;
    overflow: hidden; box-shadow: 0 3px 8px rgba(0,0,0,0.5);
  }
  .card-front { top: 92px; background: var(--white); }
  .card-back {
    top: 472px;
    background: radial-gradient(ellipse 60% 75% at 50% 35%, var(--bright) 0%, var(--blue) 45%, var(--navy) 100%);
  }

  .header-art {
    position: absolute; left: 0; top: 0; width: 600px; height: 100px;
    background: radial-gradient(ellipse 55% 120% at 50% 0%, var(--bright) 0%, var(--blue) 50%, var(--navy) 100%);
  }

  .holder { position: absolute; right: 45px; top: 14px; text-align: right; color: var(--white); font-family: "Cinzel", Georgia, serif; font-weight: 600; }
  .holder-name { font-size: 22px; line-height: 28px; letter-spacing: 0.5px; }
  .holder-role { font-size: 17px; line-height: 22px; }

  .brand { position: absolute; display: flex; align-items: center; gap: 10px; font-weight: 600; letter-spacing: 2px; }
  .brand-dot { width: 14px; height: 14px; border-radius: 50%; }
  .brand-front { left: 40px; top: 202px; color: var(--navy); font-size: 40px; }
  .brand-front .brand-dot { background: var(--navy); }
  .brand-back { left: 0; right: 0; top: 140px; justify-content: center; color: var(--white); font-size: 46px; }
  .brand-back .brand-dot { background: var(--white); }

  .divider { position: absolute; left: 295px; top: 150px; width: 1px; height: 162px; background: var(--rule); }

  .details { position: absolute; left: 318px; top: 144px; color: var(--ink); font-size: 14.5px; line-height: 19.5px; }
  .address { margin-bottom: 6px; }
  .contact-list { list-style: none; }
  .contact-list li { display: flex; align-items: center; gap: 8px; height: 22px; }
  .contact-list svg { width: 14px; height: 14px; flex: none; fill: var(--navy); }

  .tagline { position: absolute; left: 0; right: 0; top: 278px; text-align: center; color: var(--white); font-style: italic; font-size: 16px; letter-spacing: 0.3px; }
</style>
</head>
<body>

<section class="card card-front">
  <div class="header-art" role="img" aria-label="Decorative blue wave header with grey accent sweep"></div>

  <div class="holder">
    <div class="holder-name">Daniel Hartley</div>
    <div class="holder-role">Director</div>
  </div>

  <div class="brand brand-front"><span class="brand-dot"></span>KESTREL</div>

  <div class="divider"></div>

  <div class="details">
    <p class="address">Kestrel Services Ltd<br>14 Mill Parade, Elmfield Road<br>Brookford, BF27LK</p>
    <ul class="contact-list">
      <li><svg viewBox="0 0 16 16"><path d="M3 1 L6 1 L7 5 L5 6.5 C6 9 7.5 10.5 9.5 11 L11 9 L15 10 L15 13 C15 14 14 15 13 15 C6 14 2 10 1 3 C1 2 2 1 3 1 Z"/></svg>020 7946 0321</li>
      <li><svg viewBox="0 0 16 16"><path d="M4 1 H12 V5 H4 Z M1 6 H15 V12 H12 V15 H4 V12 H1 Z M5 10 V14 H11 V10 Z"/></svg>020 7946 0875</li>
      <li><svg viewBox="0 0 16 16"><path d="M4 0 H12 C13 0 13 1 13 1 V15 C13 16 12 16 12 16 H4 C3 16 3 15 3 15 V1 C3 0 4 0 4 0 Z M5 2 V10 H11 V2 Z"/></svg>07700900412</li>
      <li><svg viewBox="0 0 16 16"><path d="M1 3 H15 V13 H1 Z M2 4 L8 9 L14 4 Z" fill-rule="evenodd"/></svg>danielhartley@kestrelservices.co.uk</li>
      <li><svg viewBox="0 0 16 16"><path d="M8 1 A7 7 0 1 0 8 15 A7 7 0 1 0 8 1 Z M8 2.3 A5.7 5.7 0 1 1 8 13.7 A5.7 5.7 0 1 1 8 2.3 Z M7.4 2 H8.6 V14 H7.4 Z M2 7.4 H14 V8.6 H2 Z"/></svg>www.kestrelservices.co.uk</li>
    </ul>
  </div>
</section>

<section class="card card-back">
  <div class="brand brand-back"><span class="brand-dot"></span>KESTREL</div>
  <p class="tagline">Plumbing and Heating Services</p>
</section>

</body>
</html>
```